I need a SEO-friendly Wordpress website (making sure to style H1, H2, H3, etc correctly) for a Hawaii-based law firm called Meridian Crest Legal Group. Comparable websites include https://brvlaw.example/ and https://www.lomrit.example/ for design reference. The current copy on the TarnAdvocate.example website can be used.

```html
<!DOCTYPE html>
<html lang="en">
<head>
<meta charset="utf-8">
<title>Meridian Crest Legal Group — Kona Lawyers</title>
<link rel="stylesheet" href="https://fonts.googleapis.com/css2?family=Open+Sans:wght@400;600;700;800&display=swap">
<style>
:root{
  --brand:#6b1d08;
  --brand-deep:#4a1206;
  --rust:#a0450b;
  --btn:#7a1f08;
  --orange:#c2600f;
  --ink:#1b1b1b;
  --text:#3a3a3a;
  --white:#ffffff;
  --black:#0c0c0c;
  --star:#f2a516;
  --band:#2a2a2a;
}
*{box-sizing:border-box;margin:0;padding:0}
html,body{width:1200px;height:4739px;overflow:hidden}
body{font-family:"Open Sans",Arial,sans-serif;color:var(--text);background:var(--white);position:relative}
.section{position:absolute;left:0;width:1200px}
a{color:inherit;text-decoration:none}
.btn{display:inline-block;background:var(--btn);color:var(--white);font-weight:700;font-size:15px;text-align:center}

/* header */
.site-header{top:0;height:107px;background:var(--brand)}
.brand{position:absolute;left:98px;top:18px;color:var(--white)}
.brand-name{font-size:27px;font-weight:700;letter-spacing:.3px}
.brand-tag{font-size:15px;font-weight:600;margin-top:8px}
.call{position:absolute;left:936px;top:16px;display:flex;align-items:center;gap:10px;color:var(--white)}
.call-icon{width:34px;height:34px;border-radius:50%;background:var(--white);display:flex;align-items:center;justify-content:center}
.call small{display:block;font-size:12px}
.call strong{font-size:14px}
.main-nav{position:absolute;left:533px;top:69px;display:flex;gap:21px;color:var(--white);font-size:15px;font-weight:700}

/* hero */
.hero{top:107px;height:662px;overflow:hidden}
.hero-photo{position:absolute;inset:0;background:
  linear-gradient(180deg,rgba(0,0,0,.10),rgba(0,0,0,.25) 60%,rgba(0,0,0,.45)),
  linear-gradient(100deg,#7d5a44 0%,#a27a5f 22%,#5b4a42 42%,#8c7565 60%,#b39072 78%,#5e4638 100%);}
.hero-photo::after{content:"";position:absolute;left:0;right:0;bottom:0;height:300px;background:linear-gradient(180deg,rgba(30,28,30,0),#1d1d20 85%)}
.hero h1{position:absolute;left:0;width:1200px;top:250px;text-align:center;color:var(--white);font-size:52px;font-weight:800;line-height:58px;letter-spacing:.5px;text-shadow:0 2px 8px rgba(0,0,0,.35)}
.hero .btn{position:absolute;left:538px;top:386px;width:142px;height:40px;line-height:40px;font-size:15px}
.arrow{position:absolute;top:320px}

/* about */
.about{top:769px;height:681px}
.about-block{position:absolute;left:0;top:99px;width:362px;height:479px;background:var(--rust)}
.about-photo{position:absolute;left:144px;top:188px;width:384px;height:302px;background:linear-gradient(90deg,#bdb4ab 0%,#9d948c 45%,#3a3b42 62%,#2c2d33 78%,#a89f96 100%)}
.accent-band{position:absolute;left:364px;width:84px;height:56px;border-top:3px solid var(--band);border-bottom:3px solid var(--band)}
.about-copy{position:absolute;left:622px;top:98px;width:480px}
.about-copy h2{font-size:29px;font-weight:700;color:var(--ink);line-height:40px;margin-bottom:24px}
.about-copy p{font-size:14.5px;line-height:25.5px;text-align:justify;margin-bottom:18px}
.about-copy .btn{width:134px;height:42px;line-height:42px;font-weight:400;font-size:15px;margin-top:8px}

/* practice */
.practice{top:1450px;height:633px;background:linear-gradient(120deg,#f6f6f6,#e2e2e2 40%,#f0f0f0 60%,#cfcfcf)}
.section-title{text-align:center;font-size:31px;font-weight:700;color:var(--ink)}
.practice .section-title{position:absolute;top:72px;width:100%}
.practice-card{position:absolute;width:493px;height:185px;background:var(--white);display:flex}
.practice-card .pic{width:200px;height:185px;flex:none}
.practice-card .body{padding:30px 30px 0 34px}
.practice-card h3{font-size:14px;font-weight:700;color:var(--ink);margin-bottom:13px}
.practice-card p{font-size:14px;line-height:19px;margin-bottom:6px}
.read{font-size:15px;font-weight:700;color:var(--btn)}

/* blog */
.blog{top:2083px;height:631px}
.blog .section-title{position:absolute;top:95px;width:100%}
.blog .lead{position:absolute;top:148px;width:100%;text-align:center;font-size:15px;line-height:20px}
.blog-card{position:absolute;top:217px;width:326px;height:238px;color:var(--white)}
.blog-card h3{position:absolute;left:17px;bottom:42px;font-size:13px;font-weight:700}
.blog-card time{position:absolute;left:17px;bottom:18px;font-size:13px}
.blog .btn{position:absolute;left:532px;top:484px;width:136px;height:42px;line-height:42px}

/* team */
.team{top:2714px;height:644px;background:radial-gradient(ellipse at 20% 60%,#5a1a0a,var(--brand-deep) 55%,#2a0a04)}
.team .section-title{position:absolute;top:48px;width:100%;color:var(--white)}
.member{position:absolute;top:138px;width:326px;background:var(--white);text-align:center}
.member .pic{height:236px}
.member h3{font-size:14px;font-weight:700;color:var(--ink);margin:18px 0 12px}
.member p{font-size:14px;line-height:19px;padding:0 20px 30px}
.member .social{display:flex;justify-content:center;gap:8px;margin:-18px 0 18px}
.member .social span{width:12px;height:12px;border-radius:50%;background:var(--ink)}
.member .btn{width:144px;height:36px;line-height:36px;margin-bottom:18px;font-size:15px}

/* testimonials */
.testimonials{top:3358px;height:456px}
.testimonials .section-title{position:absolute;top:96px;width:100%;font-family:Arial,"Open Sans",sans-serif}
.quote{position:absolute;top:212px;width:450px}
.quote .avatar{position:absolute;left:0;top:0;width:70px;height:70px;border-radius:50%}
.quote p{margin-left:86px;font-size:13.5px;line-height:21px;color:var(--ink)}
.stars{margin:8px 0 0 84px;display:flex;gap:2px}
.quote .who{margin-left:82px;margin-top:10px;font-size:14px;line-height:20px;color:var(--ink)}

/* contact form */
.contact{top:3814px;height:556px;background:radial-gradient(ellipse at 50% 40%,#2a1d1a,var(--black) 70%)}
.contact-form{position:absolute;left:217px;top:50px;width:755px;height:427px;border:3px solid var(--white)}
.field{position:absolute;left:56px;display:flex;align-items:center}
.field label{width:150px;color:var(--white);font-weight:700;font-size:15px}
.field .input{width:466px;height:42px;background:#e4e4e4;font-size:13px;color:#333;padding:13px 24px}
.field .area{height:108px}
.contact-form .btn{position:absolute;top:348px;width:141px;height:42px;line-height:42px}

/* footer */
.site-footer{top:4370px;height:313px;background:#1a1a1a;color:var(--white)}
.footer-col{position:absolute;top:95px}
.footer-col h4{font-size:19px;font-weight:700;margin-bottom:16px}
.footer-col p,.footer-col li{font-size:14px;line-height:21px}
.footer-col ul{list-style:none}
.footer-col li{line-height:25.5px}
.circles{display:flex;gap:7px;margin-top:10px}
.circles span{width:28px;height:28px;border-radius:50%;border:2px solid var(--white)}
.contact-line{display:flex;gap:10px;margin-bottom:14px;font-size:14px;line-height:21px}
.copyright{top:4683px;height:56px;background:#262626;color:var(--white);text-align:center;font-size:14px;line-height:56px}
</style>
</head>
<body>

<header class="section site-header">
  <div class="brand">
    <div class="brand-name">MERIDIAN CREST LEGAL GROUP</div>
    <div class="brand-tag">DIVORCE AND PERSONAL INJURY LAWYERS</div>
  </div>
  <div class="call">
    <span class="call-icon"><svg width="18" height="18" viewBox="0 0 24 24"><path d="M6.6 10.8a15 15 0 0 0 6.6 6.6l2.2-2.2a1 1 0 0 1 1-.25 11 11 0 0 0 3.6.6 1 1 0 0 1 1 1V20a1 1 0 0 1-1 1A17 17 0 0 1 3 4a1 1 0 0 1 1-1h3.5a1 1 0 0 1 1 1 11 11 0 0 0 .6 3.6 1 1 0 0 1-.25 1z" fill="none" stroke="#6b1d08" stroke-width="1.6"/></svg></span>
    <div><small>CALL NOW</small><strong>+1.808.555.0148</strong></div>
  </div>
  <nav class="main-nav"><a>HOME</a><a>ABOUT</a><a>PRACTICE AREAS</a><a>ATTORNEYS</a><a>BLOG</a><a>CONTACT US</a></nav>
</header>

<section class="section hero">
  <div class="hero-photo" role="img" aria-label="Team of smiling lawyers working around a laptop in a wood-panelled office"></div>
  <h1>KONA LAWYERS OF<br>MCLG - LEGAL</h1>
  <a class="btn">GET STARTED</a>
  <svg class="arrow" style="left:52px" width="16" height="28" viewBox="0 0 16 28"><path d="M14 2 2 14l12 12" fill="none" stroke="#fff" stroke-width="2"/></svg>
  <svg class="arrow" style="left:1144px" width="16" height="28" viewBox="0 0 16 28"><path d="M2 2l12 12L2 26" fill="none" stroke="#fff" stroke-width="2"/></svg>
</section>

<section class="section about">
  <div class="about-block"></div>
  <div class="accent-band" style="top:114px"></div>
  <div class="accent-band" style="top:500px"></div>
  <div class="about-photo" role="img" aria-label="Lawyer in a dark suit holding a folder on courthouse steps"></div>
  <div class="about-copy">
    <h2>ABOUT THE KONA LAWYERS OF MCLG</h2>
    <p>The experienced attorneys in the Meridian Crest Legal Group's Kailua Kona, Hawaii office provide clients with a wide range of litigation expertise, including legal claims involving divorce &amp; family, personal injury, toxic exposures, intellectual property, and real estate.</p>
    <p>Our Kona office also offers commercial and hospitality litigation expertise on behalf of a wide variety of clients, including restaurants, hotels, property owners, and many others. We never wish to see our clients go to court, though if there is no other option, you're in safe hands with our seasoned trial lawyers and the many years of courtroom experience behind them.</p>
    <a class="btn">Learn More</a>
  </div>
</section>

<section class="section practice">
  <h2 class="section-title">AREAS OF PRACTICE</h2>
  <article class="practice-card" style="left:98px;top:165px">
    <div class="pic" role="img" aria-label="Mother hugging her daughter" style="background:linear-gradient(135deg,#e7c7b3 0%,#b98a74 40%,#8a2c22 70%,#4a2a26 100%)"></div>
    <div class="body"><h3>FAMILY &amp; DIVORCE</h3><p>Our lawyers handle all aspects of family law on the Big Island than 70 years of combined</p><a class="read">Read More</a></div>
  </article>
  <article class="practice-card" style="left:607px;top:165px">
    <div class="pic" role="img" aria-label="Damaged car after an accident" style="background:linear-gradient(160deg,#c9c9c7 0%,#8b8c8e 35%,#3a3b3e 65%,#18191b 100%)"></div>
    <div class="body"><h3>PERSONAL INJURY</h3><p>Dealing with personal injury and wrongful death claims is hard enough</p><a class="read">Read More</a></div>
  </article>
  <article class="practice-card" style="left:98px;top:368px">
    <div class="pic" role="img" aria-label="Two businessmen reviewing documents" style="background:linear-gradient(135deg,#d9d6d1 0%,#a69a8e 40%,#3c4048 70%,#23262b 100%)"></div>
    <div class="body"><h3>CORPORATE &amp; IP</h3><p>The attorneys at MCLG have been helping Big Island business owners with all their legal</p><a class="read">Read More</a></div>
  </article>
  <article class="practice-card" style="left:607px;top:368px">
    <div class="pic" role="img" aria-label="White front door of a house" style="background:linear-gradient(90deg,#8a7456 0%,#e9e2c8 25%,#f7f4ea 50%,#e4dcc0 75%,#7d6a4c 100%)"></div>
    <div class="body"><h3>REAL ESTATE</h3><p>Our lawyers work with home owners, buyers and property developers</p><a class="read">Read More</a></div>
  </article>
</section>

<section class="section blog">
  <h2 class="section-title">LATEST BLOG</h2>
  <p class="lead">Sed ut perspiciatis unde omnis iste natus error sit voluptatem<br>accusantium doloremque laudantium</p>
  <svg class="arrow" style="left:36px;top:323px" width="12" height="22" viewBox="0 0 12 22"><path d="M11 1 1 11l10 10" fill="none" stroke="#333" stroke-width="1.6"/></svg>
  <article class="blog-card" style="left:99px;background:linear-gradient(120deg,#1c1616 0%,#4a3a36 30%,#b8501f 62%,#7a2a14 82%,#1a1212 100%)" role="img" aria-label="Lawyer speaking with a client in custody">
    <h3>Make Every Effort to Make It Work</h3><time>25 May 2019</time>
  </article>
  <article class="blog-card" style="left:436px;background:linear-gradient(135deg,#4a4644 0%,#2e2b2a 50%,#1b1918 100%)" role="img" aria-label="Lawyer in a suit at his desk">
    <h3 style="bottom:auto;top:100px">Interview Divorce Lawyers</h3><time style="bottom:auto;top:125px">25 May 2019</time>
  </article>
  <article class="blog-card" style="left:773px;background:linear-gradient(90deg,#5c6068 0%,#c9ccd0 35%,#eef0f1 55%,#a9a5a2 78%,#4a4a4e 100%)" role="img" aria-label="Couple receiving keys from an advisor">
    <h3>Put Together Your Assets and Debts</h3><time>25 May 2019</time>
  </article>
  <svg class="arrow" style="left:1152px;top:323px" width="12" height="22" viewBox="0 0 12 22"><path d="M1 1l10 10L1 21" fill="none" stroke="#333" stroke-width="1.6"/></svg>
  <a class="btn">View All</a>
</section>

<section class="section team">
  <h2 class="section-title">OUR TEAM</h2>
  <article class="member" style="left:99px">
    <div class="pic" role="img" aria-label="Portrait of attorney Martin Okafor" style="background:linear-gradient(180deg,#f3f3f3 0%,#c9c6c4 40%,#5a5656 70%,#141416 100%)"></div>
    <h3>MARTIN OKAFOR</h3>
    <p>Martin Okafor graduated from the Westbrook University College of Law, in 1971</p>
  </article>
  <article class="member" style="left:438px">
    <div class="pic" role="img" aria-label="Portrait of attorney Gerald Stavros" style="background:linear-gradient(180deg,#565452 0%,#8e7f72 35%,#2c3f70 70%,#1c2a4e 100%)"></div>
    <h3>GERALD STAVROS</h3>
    <p>Gerald Stavros graduated from the Westbrook University College of Law, in 1972.</p>
    <div class="social"><span></span><span></span><span></span></div>
    <a class="btn">Read More</a>
  </article>
  <article class="member" style="left:775px">
    <div class="pic" role="img" aria-label="Portrait of attorney in an office" style="background:linear-gradient(90deg,#dcdcd8 0%,#f2f1ee 30%,#9c8f86 50%,#2d2f36 70%,#e6e5e1 100%)"></div>
    <h3>GERALD</h3>
    <p>Gerald Stavros graduated from the Westbrook University College of Law, in 1972.</p>
  </article>
</section>

<section class="section testimonials">
  <h2 class="section-title">TESTIMONIALS</h2>
  <svg class="arrow" style="left:50px;top:222px" width="12" height="22" viewBox="0 0 12 22"><path d="M11 1 1 11l10 10" fill="none" stroke="#333" stroke-width="1.6"/></svg>
  <blockquote class="quote" style="left:98px">
    <div class="avatar" role="img" aria-label="Client portrait" style="background:linear-gradient(160deg,#e8d4b8,#8a8f9e 55%,#2c3550)"></div>
    <p>Lorem Ipsum is simply dummy text of the printing and typesetting industry. Lorem Ipsum has been the industry's standard dummy text</p>
    <div class="stars">
      <svg width="84" height="14" viewBox="0 0 84 14"><g fill="#f2a516"><path id="s" d="M7 0l2.1 4.6 4.9.5-3.7 3.3 1.1 4.9L7 10.8 2.6 13.3l1.1-4.9L0 5.1l4.9-.5z"/><use href="#s" x="17"/><use href="#s" x="34"/><use href="#s" x="51"/><use href="#s" x="68"/></g></svg>
    </div>
    <div class="who">Selina Marsh<br>CEO</div>
  </blockquote>
  <blockquote class="quote" style="left:615px">
    <div class="avatar" role="img" aria-label="Client portrait" style="background:linear-gradient(160deg,#d9d9d9,#6d6a68 50%,#1a1a1c)"></div>
    <p>Lorem Ipsum is simply dummy text of the printing and typesetting industry. Lorem Ipsum has been the industry's standard dummy text</p>
    <div class="stars">
      <svg width="84" height="14" viewBox="0 0 84 14"><g fill="#f2a516"><use href="#s"/><use href="#s" x="17"/><use href="#s" x="34"/><use href="#s" x="51"/><use href="#s" x="68"/></g></svg>
    </div>
    <div class="who">Corin Vale<br>Finanace</div>
  </blockquote>
  <svg class="arrow" style="left:1140px;top:222px" width="12" height="22" viewBox="0 0 12 22"><path d="M1 1l10 10L1 21" fill="none" stroke="#333" stroke-width="1.6"/></svg>
</section>

<section class="section contact">
  <form class="contact-form">
    <div class="field" style="top:42px"><label>Your Name</label><div class="input">Enter Your Name</div></div>
    <div class="field" style="top:102px"><label>Email Address</label><div class="input">Enter Email</div></div>
    <div class="field" style="top:162px"><label>Mobile Number</label><div class="input">Enter Your Number</div></div>
    <div class="field" style="top:222px;align-items:flex-start"><label style="padding-top:12px">Message</label><div class="input area">Message</div></div>
    <a class="btn" style="left:373px">SUBMIT</a>
    <a class="btn" style="left:530px;background:var(--orange)">RESET</a>
  </form>
</section>

<footer class="section site-footer">
  <div class="footer-col" style="left:203px;width:272px">
    <h4>ABOUT</h4>
    <p style="text-align:justify">The experienced attorneys in the Meridian Crest Legal Group's Kailua Kona, Hawaii office provide clients with a wide range of litigation expertise,</p>
    <div class="circles"><span></span><span></span><span></span><span></span></div>
  </div>
  <div class="footer-col" style="left:526px">
    <h4>QUICK LINKS</h4>
    <ul><li>Home</li><li>About</li><li>Practice Areas</li><li>Attorneys</li><li>Blog</li><li>Contact us</li></ul>
  </div>
  <div class="footer-col" style="left:758px;width:300px">
    <h4>CONTACT US</h4>
    <div class="contact-line"><svg width="12" height="16" viewBox="0 0 12 16"><path d="M6 0a6 6 0 0 0-6 6c0 4.5 6 10 6 10s6-5.5 6-10a6 6 0 0 0-6-6zm0 8.3A2.3 2.3 0 1 1 6 3.7a2.3 2.3 0 0 1 0 4.6z" fill="#fff"/></svg><span>48 2210 Lanakila Road, Suite 310<br>Kailua Kona, Hawaii 96745.</span></div>
    <div class="contact-line"><svg width="14" height="14" viewBox="0 0 24 24"><path d="M6.6 10.8a15 15 0 0 0 6.6 6.6l2.2-2.2a1 1 0 0 1 1-.25 11 11 0 0 0 3.6.6 1 1 0 0 1 1 1V20a1 1 0 0 1-1 1A17 17 0 0 1 3 4a1 1 0 0 1 1-1h3.5a1 1 0 0 1 1 1 11 11 0 0 0 .6 3.6 1 1 0 0 1-.25 1z" fill="none" stroke="#fff" stroke-width="2"/></svg><span>1.808.555.0148</span></div>
    <div class="contact-line"><svg width="14" height="12" viewBox="0 0 14 12"><rect x="1" y="1" width="12" height="10" fill="none" stroke="#fff" stroke-width="1.3"/><path d="M1 1l6 5 6-5" fill="none" stroke="#fff" stroke-width="1.3"/></svg><span>clients@tarnadvocate.example</span></div>
  </div>
</footer>

<div class="section copyright">Copyrights © 2019 All Rights Reserved</div>

</body>
</html>
```